Teeth Whitening Clinic Website Redesign - Social Proof Theme

NEW TEETH SITEREVAMP CURRENT WEBSITE:WWW.SANDIEGOSTEETHWHITENING.COMTHEME:SOCIAL PROOF/5 STAR REVIEWS/TESTIMONIALS THEME:https://maps.example.net/QxRvPLoKzN84 I want a testimonial themed, social proof themed website so customers will be sold by testimonials all over the website….I like a nice clean simple site but with all important factors standing out like CALLS TO ACTIONS, for example the $99 special link in header on original design. Also, testimonials throughout the website placed methodically as not to be FORCED and CLUTTEREDKeep all same exact content for all pages and elements of current design. All buttons, calls to action, navigation, etc. Please do not leave anything out from current design. SPECIAL INSTRUCTIONS for banner image:I want to use actual customer photos inside the banner image in a way that really pops and grabs attention. Please grab some customer photos from my PG Account, fk or rateway account: Also, I want to integrate 5 star rateway logo, friendbook review 5 stars icon, searchly business page 5 stars icon, etc. on the banner as well to show social proof as much as possible. Actual customer photos to be used throughout website:https://www.photogram.example/brightharborsmilestudioplace/ https://www.friendbook.com/SDTeethWhitening/https://www.reviewhub.example/biz/bright-harbor-smile-studio-place-bright-harbor-5 Reviews:https://www.reviewhub.example/biz/bright-harbor-smile-studio-place-bright-harbor-5 https://www.friendbook.com/pg/SDTeethWhitening/reviews/?ref=page_internalhttps://goo.gl/maps/TmJcABLAJwC2 Please do home page first to come up with theme then after approval home page we can move forward additional pages.

Target Market(s)

PEOPLE THAT CARE ABOUT DENTAL HYGEINE AND OR CARE ABOUT THEIR TEETH SMILE

Industry/Entity Type

Dental Clinic

Number of Pages Required

5+ page

Colors

Designer to choose colors to be used in the design.

Requirements
Must have
• NEW TEETH SITE
• REVAMP CURRENT WEBSITE:
• WWW.BRIGHTHARBORSMILESTUDIO.EXAMPLE
• THEME:
• SOCIAL PROOF/5 STAR REVIEWS/TESTIMONIALS THEME:
• https://maps.example.net/QxRvPLoKzN84
• I want a testimonial themed, social proof themed website so customers will be sold by testimonials all over the website….I like a nice clean simple site but with all important factors standing out like CALLS TO ACTIONS, for example the $99 special link in header on original design. Also, testimonials throughout the website placed methodically as not to be FORCED and CLUTTERED
• Keep all same exact content for all pages and elements of current design. All buttons, calls to action, navigation, etc. Please do not leave anything out from current design.
• SPECIAL INSTRUCTIONS for banner image:
• I want to use actual customer photos inside the banner image in a way that really pops and grabs attention. Please grab some customer photos from my PG Account, fk or rateway account:
• Also, I want to integrate 5 star rateway logo, friendbook review 5 stars icon, searchly business page 5 stars icon, etc. on the banner as well to show social proof as much as possible.
• Actual customer photos to be used throughout website:
• https://www.photogram.example/brightharborsmilestudioplace/
• https://www.friendbook.example/BHSmileStudio/
• https://www.reviewhub.example/biz/bright-harbor-smile-studio-place-bright-harbor-5
• Reviews:
• https://www.friendbook.example/pg/BHSmileStudio/reviews/?ref=page_internal
• Please do home page first to come up with theme then after approval home page we can move forward additional pages.
Nice to have
• NEW TEETH SITE
• REVAMP CURRENT WEBSITE:
• THEME:
• Reviews:
Should not have
• NEW TEETH SITE
• REVAMP CURRENT WEBSITE:
• THEME:
• Reviews:

```html
<!DOCTYPE html>
<html lang="en">
<head>
<meta charset="utf-8">
<title>Bright Harbor Smile Studio</title>
<link href="https://fonts.googleapis.com/css2?family=Poppins:ital,wght@0,400;0,500;0,600;0,700;1,400&family=Cinzel:wght@700&family=Roboto+Condensed:wght@700&display=swap" rel="stylesheet">
<style>
:root{
  --blue:#0aa2cf;
  --blue-dark:#0b86ad;
  --ink:#222;
  --body:#444;
  --muted:#666;
  --gray:#636363;
  --pale:#f4f4f4;
  --footer:#333;
  --white:#fff;
  --star:#d32323;
}
*{margin:0;padding:0;box-sizing:border-box}
html,body{width:1200px;height:3862px;overflow:hidden}
body{font-family:"Poppins",sans-serif;color:var(--body);background:var(--white);position:relative}
.abs{position:absolute}
a{color:inherit;text-decoration:none}

/* top bar */
.topbar{top:0;left:0;width:1200px;height:32px;background:var(--gray)}
.social{left:110px;top:7px;display:flex;gap:10px;color:#ddd;font-size:13px;font-weight:600}
.phone-tab{right:118px;top:0;height:32px;width:188px;background:var(--blue);color:#fff;font-size:15px;font-weight:500;display:flex;align-items:center;justify-content:center;gap:8px;clip-path:polygon(14px 0,100% 0,calc(100% - 14px) 100%,0 100%)}

/* header */
.brand{left:110px;top:52px;display:flex;align-items:center;gap:10px}
.brand .mark{width:56px;height:56px;border-radius:50%;background:#e4eef2}
.brand span{font-size:21px;font-weight:500;color:var(--gray);line-height:1.1}
.info{top:62px;display:flex;align-items:flex-start;gap:14px;font-size:14.5px;color:var(--ink);line-height:22px}
.info svg{flex:none}

/* nav */
.nav{top:138px;left:0;width:1200px;height:50px;background:var(--blue)}
.nav ul{list-style:none;position:absolute;left:110px;top:0;display:flex;height:50px}
.nav li{color:#fff;font-size:14.5px;padding:0 10px;line-height:50px}
.nav li.on{background:var(--blue-dark);padding:0 12px}
.book-box{left:918px;top:132px;width:168px;height:62px;background:#fff;color:var(--blue);font-size:14px;text-align:center;line-height:20px;padding-top:11px;box-shadow:0 0 0 3px rgba(10,162,207,.3)}

/* hero */
.hero{top:188px;left:0;width:1200px;height:562px;background:linear-gradient(180deg,#5b4d4a,#6e5e5a 45%,#7a6a66);overflow:hidden}
.hero .shade{inset:0;background:rgba(30,25,25,.35)}
.hero h1{top:108px;left:0;width:1200px;text-align:center;font-family:"Cinzel",serif;color:#fff;font-size:45px;line-height:52px;letter-spacing:1px}
.hero .sub{top:234px;left:330px;width:540px;text-align:center;color:#fff;font-size:16.5px;line-height:28px;font-weight:500}
.btn-white{top:324px;left:446px;width:146px;height:50px;background:#fff;color:var(--ink);font-size:15.5px;font-weight:500;display:flex;align-items:center;justify-content:center}
.btn-ghost{top:324px;left:608px;width:146px;height:50px;border:2px solid #fff;color:#fff;font-size:15.5px;font-weight:500;display:flex;align-items:center;justify-content:center}
.arc{left:0;top:440px}
.badges{top:493px;left:412px;display:flex;gap:30px;align-items:center}
.badge{display:flex;flex-direction:column;align-items:center;gap:4px;font-size:17px;font-weight:600;color:var(--ink)}
.badge .row{display:flex;gap:2px}
.badge .row i{width:18px;height:18px;background:var(--star);display:block}
.badge .row.gold i{background:#e9a825;width:13px;height:13px;border-radius:50%}

/* intro */
.intro-mark{left:570px;top:835px;width:60px;height:60px;border-radius:50%;background:#e4eef2;border:2px solid #d3dde2}
.h2{color:var(--blue);font-weight:700;font-size:28px;text-align:center;left:0;width:1200px}
.tag{top:960px;left:0;width:1200px;text-align:center;font-size:17px;color:var(--ink)}
.intro-p{top:1014px;left:110px;width:980px;text-align:center;font-size:13px;line-height:26px;color:var(--body)}
.btn-blue{background:var(--blue);color:#fff;font-size:15px;font-weight:600;display:flex;align-items:center;justify-content:center}

/* how it works */
.how-band{top:1330px;left:0;width:1200px;height:478px;background:var(--pale)}
.how-strip{top:1330px;left:0;width:111px;height:478px;background:linear-gradient(180deg,#3cc0e0,#1aa6cf)}
.video{top:1286px;left:111px;width:450px;height:564px;background:linear-gradient(180deg,#6b6b6b,#5a5a5a)}
.play{left:180px;top:236px}
.how-h{top:1388px;left:595px;color:var(--blue);font-size:28px;font-weight:700}
.how-rule{top:1440px;left:595px;width:66px;height:2px;background:var(--blue)}
.how-p{left:595px;width:495px;font-size:13px;line-height:23px;color:var(--body)}

/* why */
.rule-c{left:561px;width:78px;height:2px;background:var(--blue)}
.pill{height:80px;border-radius:40px;color:#fff;font-family:"Roboto Condensed",sans-serif;font-weight:700;font-size:24px;display:flex;align-items:center}
.pill.b{background:var(--blue)}
.pill.g{background:var(--gray)}
.pill.l{justify-content:flex-end;padding-right:8px}
.pill.r{padding-left:8px}
.pill .ic{width:66px;height:66px;border-radius:50%;background:#fff;display:flex;align-items:center;justify-content:center}
.pill.l .ic{margin-left:18px}
.pill.r .ic{margin-right:18px}
.dot{width:16px;height:16px;border-radius:50%;background:#fff;border:3px solid var(--blue)}
.dot.g{border-color:var(--gray)}
.center-logo{left:505px;top:2200px;display:flex;align-items:center;gap:8px}
.center-logo .mark{width:40px;height:40px;border-radius:50%;background:#e4eef2}
.center-logo span{font-size:16px;font-weight:500;color:var(--gray);line-height:1.15}

/* compare */
.compare-band{top:2470px;left:0;width:1200px;height:670px;background:var(--pale)}
.col{background:#fff;border-bottom:5px solid #555;box-shadow:0 0 6px rgba(0,0,0,.12);text-align:center}
.col .head{background:#555;color:#fff;font-family:"Roboto Condensed",sans-serif;font-weight:700;display:flex;align-items:center;justify-content:center}
.col ul{list-style:none;padding:8px 10px 0}
.col li{border-bottom:1px solid #e5e5e5;color:var(--body)}
.col li:last-child{border-bottom:none}
.col .cap{position:absolute;left:50%;transform:translateX(-50%);border-radius:50%;background:#e4eef2;border:3px solid #fff}
.col.star{border-bottom:7px solid var(--blue)}
.col.star .head{background:var(--blue)}

/* testimonials */
.quote-blob{left:196px;top:3260px;width:172px;height:172px;border-radius:50%;background:var(--blue)}
.avatar{left:112px;top:3262px;width:166px;height:166px;border-radius:50%;background:linear-gradient(160deg,#8a6550,#5a3e30);border:4px solid #fff}
.t-h{top:3240px;left:402px;color:var(--blue);font-size:28px;font-weight:700}
.t-q{top:3302px;left:402px;font-style:italic;font-size:15.5px;line-height:27px;color:var(--ink)}
.t-stars{top:3368px;left:404px;display:flex;gap:2px;align-items:center}
.t-stars i{width:14px;height:14px;background:var(--star);display:block}
.t-stars span{margin-left:14px;font-size:14px;color:var(--ink)}
.t-name{top:3408px;left:402px;font-size:15px;color:var(--blue)}
.t-name small{font-size:13px;color:var(--ink)}
.dots{top:3456px;left:402px;display:flex;gap:4px}
.dots i{width:14px;height:14px;border-radius:50%;background:#cfe9f2;display:block}
.dots i:first-child{background:var(--blue)}

/* footer */
.footer{top:3558px;left:0;width:1200px;height:304px;background:var(--footer);color:#fff}
.f-links{left:0;width:1200px;text-align:center;font-size:15.5px;font-weight:500;line-height:32px}
.f-links b{font-weight:400;margin:0 10px}
.f-rule{left:111px;top:237px;width:978px;height:1px;background:#555}
.copy{top:258px;left:0;width:1200px;text-align:center;font-size:14px;font-weight:500}
.code{top:258px;right:48px;font-size:14px}
</style>
</head>
<body>

<!-- top bar -->
<div class="abs topbar">
  <div class="abs social"><span>f</span><span>t</span><span>o</span></div>
  <div class="abs phone-tab">
    <svg width="14" height="14" viewBox="0 0 24 24" fill="#fff"><path d="M6.6 10.8a15.1 15.1 0 0 0 6.6 6.6l2.2-2.2a1 1 0 0 1 1-.25 11.4 11.4 0 0 0 3.6.6 1 1 0 0 1 1 1V20a1 1 0 0 1-1 1A17 17 0 0 1 3 4a1 1 0 0 1 1-1h3.5a1 1 0 0 1 1 1c0 1.25.2 2.45.6 3.6a1 1 0 0 1-.25 1z"/></svg>
    1-555-014-2290
  </div>
</div>

<!-- header -->
<div class="abs brand"><div class="mark"></div><span>Bright Harbor<br>Smile Studio</span></div>
<div class="abs info" style="left:476px">
  <svg width="26" height="44" viewBox="0 0 26 44"><text x="2" y="36" font-size="40" font-family="Poppins" fill="#0aa2cf">$</text></svg>
  <div>Click Here to Get Our $99 Teeth<br>Whiting Deal (Reg: $378)</div>
</div>
<div class="abs info" style="left:774px">
  <svg width="34" height="42" viewBox="0 0 34 42"><path d="M17 3a13 13 0 0 0-13 13c0 10 13 23 13 23s13-13 13-23A13 13 0 0 0 17 3z" fill="none" stroke="#0aa2cf" stroke-width="3"/><circle cx="17" cy="16" r="5" fill="none" stroke="#0aa2cf" stroke-width="3"/></svg>
  <div>location4410 Harbor View Rd. #118<br>Bayport, CA 90000</div>
</div>

<!-- nav -->
<nav class="abs nav">
  <ul>
    <li class="on">Home</li><li>Our Process</li><li>Photos</li><li>Free Treatments</li><li>Testimonials</li><li>Blog</li><li>FAQ</li><li>Contact</li><li>Gift Certificates</li>
  </ul>
</nav>
<div class="abs book-box">Book<br>Appointment Online</div>

<!-- hero -->
<section class="abs hero">
  <div class="abs" style="inset:0" role="img" aria-label="Collage of happy customers holding smile signs after whitening"></div>
  <div class="abs shade"></div>
  <h1 class="abs">Get That White Smile You've<br>Always Wanted</h1>
  <p class="abs sub">Amazing Results, The Most Effective System, More Affordable Than The Dentist</p>
  <a class="abs btn-white">Book Online</a>
  <a class="abs btn-ghost">Contact Us</a>
  <svg class="abs arc" width="1200" height="122" viewBox="0 0 1200 122"><path d="M300 122 C420 10 780 10 1000 122 Z" fill="#fff"/></svg>
  <div class="abs badges">
    <div class="badge">rateway<div class="row"><i></i><i></i><i></i><i></i><i></i></div></div>
    <div class="badge">friendbook<div class="row gold"><i></i><i></i><i></i><i></i><i></i></div></div>
    <div class="badge" style="flex-direction:row;gap:8px">searchly<span style="width:22px;height:22px;background:#4a7fe0;border-radius:4px;display:block"></span></div>
  </div>
</section>

<!-- intro -->
<div class="abs intro-mark"></div>
<h2 class="abs h2" style="top:912px">Bright Harbor Smile Studio</h2>
<p class="abs tag">The best price, service and results.</p>
<p class="abs intro-p">Bright Harbor Smile Studio features state-of-the-art technologies that are safe, industry-unique and very cost-effective. Our teeth whitening system utilizes the latest blue light whitening technology. Our Blue Light Systems are calibrated precisely for optimal activation of our exclusive hydrogen peroxide based whitening solution which is manufactured in a FDA registered facility in the USA.</p>
<a class="abs btn-blue" style="left:537px;top:1128px;width:127px;height:44px">Read More</a>

<!-- how it works -->
<div class="abs how-band"></div>
<div class="abs how-strip" role="img" aria-label="Customer photo tinted blue"></div>
<div class="abs video" role="img" aria-label="Video thumbnail showing the studio logo">
  <svg class="abs play" width="90" height="90" viewBox="0 0 90 90"><circle cx="45" cy="45" r="42" fill="none" stroke="#fff" stroke-width="5"/><path d="M35 26 L64 45 L35 64 Z" fill="#fff"/></svg>
</div>
<h2 class="abs how-h">How It Works</h2>
<div class="abs how-rule"></div>
<p class="abs how-p" style="top:1470px">We have a very effective teeth whitening treatment that is guaranteed to get you quick results in about 1 hour. To start the treatment you'll apply a Hydrogen Peroxide based whitening agent to your teeth. We then place our cold blue light directly.</p>
<p class="abs how-p" style="top:1573px">We always perform what we call a "Triple Treatment". So that's 3 of the 15 minute treatments all done consecutively, in the same visit. The actual whitening time is a total of 45 minutes. Now there is a few minute break in between each 15 minute treatment.</p>
<a class="abs btn-blue" style="left:595px;top:1696px;width:112px;height:44px">Read More</a>

<!-- why choose us -->
<h2 class="abs h2" style="top:1938px">Why Choose Us</h2>
<div class="abs rule-c" style="top:1996px"></div>
<svg class="abs" style="left:445px;top:2066px" width="310" height="300" viewBox="0 0 310 300">
  <circle cx="155" cy="149" r="145" fill="none" stroke="#333" stroke-width="2" stroke-dasharray="6 5"/>
  <circle cx="155" cy="149" r="118" fill="#fff" stroke="#0aa2cf" stroke-width="6"/>
</svg>
<div class="abs center-logo"><div class="mark"></div><span>Bright Harbor<br>Smile Studio</span></div>

<div class="abs pill b l" style="left:170px;top:2072px;width:280px">PRICE<div class="ic"><svg width="40" height="40" viewBox="0 0 40 40"><circle cx="20" cy="20" r="17" fill="none" stroke="#0aa2cf" stroke-width="2"/><text x="13" y="29" font-size="24" font-family="Poppins" fill="#0aa2cf">$</text></svg></div></div>
<div class="abs pill g l" style="left:140px;top:2175px;width:280px">RESULTS<div class="ic"><svg width="36" height="36" viewBox="0 0 36 36" fill="none" stroke="#555" stroke-width="2.5"><path d="M4 32h28M8 30v-8M14 30v-12M20 30v-9M26 30v-16M6 18l8-7 6 5 10-10"/></svg></div></div>
<div class="abs pill b l" style="left:170px;top:2276px;width:280px">NO PAIN<div class="ic"><svg width="36" height="36" viewBox="0 0 36 36" fill="none" stroke="#0aa2cf" stroke-width="2.5"><circle cx="18" cy="18" r="14"/><circle cx="13" cy="15" r="1.5" fill="#0aa2cf"/><circle cx="23" cy="15" r="1.5" fill="#0aa2cf"/><path d="M12 22c3 3 9 3 12 0"/></svg></div></div>

<div class="abs pill b r" style="left:755px;top:2072px;width:280px"><div class="ic"><svg width="38" height="38" viewBox="0 0 38 38" fill="none" stroke="#0aa2cf" stroke-width="2.5"><path d="M10 10c4-3 8 0 9 0s5-3 9 0c3 3 1 10-1 14l-2 8-3-6-3 6-2-8c-2-4-5-11-7-14z"/></svg></div>SERVICE</div>
<div class="abs pill g r" style="left:782px;top:2175px;width:280px"><div class="ic"><svg width="38" height="38" viewBox="0 0 38 38" fill="none" stroke="#222" stroke-width="3"><path d="M6 30L26 12"/><path d="M20 8l10 10" stroke-width="6"/></svg></div>CONVENIENCE</div>
<div class="abs pill b r" style="left:755px;top:2276px;width:280px"><div class="ic"><svg width="38" height="38" viewBox="0 0 38 38" fill="none" stroke="#0aa2cf" stroke-width="2.5"><circle cx="18" cy="15" r="10"/><text x="13" y="21" font-size="15" font-family="Poppins" fill="#0aa2cf" stroke="none">$</text><path d="M4 30c6-2 10 2 16 0l8-4"/></svg></div>PRICE</div>

<div class="abs dot" style="left:469px;top:2131px"></div>
<div class="abs dot g" style="left:450px;top:2219px"></div>
<div class="abs dot" style="left:479px;top:2298px"></div>
<div class="abs dot" style="left:718px;top:2131px"></div>
<div class="abs dot g" style="left:736px;top:2219px"></div>
<div class="abs dot" style="left:709px;top:2298px"></div>

<!-- compare -->
<div class="abs compare-band"></div>
<h2 class="abs h2" style="top:2530px">Compare Us</h2>

<div class="abs col" style="left:120px;top:2715px;width:160px;height:285px">
  <div class="cap" style="top:-22px;width:42px;height:42px"></div>
  <div class="head" style="height:62px;font-size:17px;padding-top:14px">FEATURES</div>
  <ul style="font-size:13.5px"><li style="line-height:37px">Speed</li><li style="line-height:37px">Ease of Use</li><li style="line-height:37px">Cost</li><li style="line-height:37px">Availability</li><li style="line-height:37px">Pain</li></ul>
</div>
<div class="abs col" style="left:279px;top:2700px;width:187px;height:315px">
  <div class="cap" style="top:-26px;width:48px;height:48px"></div>
  <div class="head" style="height:72px;font-size:19px;padding-top:10px">LUMEN PRO</div>
  <ul style="font-size:15px"><li style="line-height:41px">1-2 Hours</li><li style="line-height:41px">Difficult / Dentist</li><li style="line-height:41px">$300 - $600</li><li style="line-height:41px">Limited Availability</li><li style="line-height:41px">Pain &amp; Sensitivity</li></ul>
</div>
<div class="abs col star" style="left:468px;top:2668px;width:251px;height:387px">
  <div class="head" style="height:92px;gap:8px;font-family:Poppins,sans-serif;font-weight:500;font-size:16px;line-height:1.15;text-align:left"><span style="width:40px;height:40px;border-radius:50%;background:#e4eef2;display:block"></span>Bright Harbor<br>Smile Studio</div>
  <ul style="font-size:18.5px;color:var(--ink)"><li style="line-height:49px">45 Mins</li><li style="line-height:49px">Very Easy</li><li style="line-height:49px">$378</li><li style="line-height:49px">Appt Only</li><li style="line-height:49px">No Pain</li></ul>
</div>
<div class="abs col" style="left:720px;top:2700px;width:196px;height:315px">
  <div class="cap" style="top:-26px;width:48px;height:48px"></div>
  <div class="head" style="height:72px;font-size:19px;padding-top:10px">GLOWCARE</div>
  <ul style="font-size:15px"><li style="line-height:41px">7-14 Days</li><li style="line-height:41px">Difficult / Dentist</li><li style="line-height:41px">$300 - $600</li><li style="line-height:41px">Limited Availability</li><li style="line-height:41px">Sensitivity</li></ul>
</div>
<div class="abs col" style="left:918px;top:2715px;width:163px;height:285px">
  <div class="cap" style="top:-22px;width:42px;height:42px"></div>
  <div class="head" style="height:62px;font-size:17px;padding-top:14px">HOME KITS</div>
  <ul style="font-size:13.5px"><li style="line-height:37px">7-30 Days</li><li style="line-height:37px">Difficult</li><li style="line-height:37px">$50 - $150</li><li style="line-height:37px">Store Purchase</li><li style="line-height:37px">Sensitivity</li></ul>
</div>

<!-- testimonials -->
<div class="abs quote-blob">
  <svg class="abs" style="left:78px;top:62px" width="70" height="50" viewBox="0 0 70 50" fill="#fff"><circle cx="16" cy="30" r="13"/><path d="M6 30 L20 4 L26 8 L16 30Z"/><circle cx="50" cy="30" r="13"/><path d="M40 30 L54 4 L60 8 L50 30Z"/></svg>
</div>
<div class="abs avatar" role="img" aria-label="Portrait photo of the reviewing customer"></div>
<h2 class="abs t-h">Our Testimonials</h2>
<p class="abs t-q">My God they are great amd Lively :) Kind and love the result!!!!!!!!<br>Definitely going back!!!:)</p>
<div class="abs t-stars"><i></i><i></i><i></i><i></i><i></i><span>9/4/2018</span></div>
<p class="abs t-name">- Dana R. <small>Seaside, CA</small></p>
<div class="abs dots"><i></i><i></i><i></i><i></i><i></i></div>

<!-- footer -->
<footer class="abs footer">
  <div class="abs f-links" style="top:76px">Home<b>|</b>Book Appointment Online<b>|</b>Our Process<b>|</b>Photos<b>|</b>Testimonials<b>|</b>Blog</div>
  <div class="abs f-links" style="top:108px">FAQ<b>|</b>Contact<b>|</b>Gift Certificates<b>|</b>After Care<b>|</b>Consent Form Espanol</div>
  <div class="abs f-links" style="top:140px">Consent Form English</div>
  <div class="abs f-rule"></div>
  <div class="abs copy">Copyrights @ 2018 Bright Harbor Smile Studio. All Rights Reserved.</div>
  <div class="abs code">C20</div>
</footer>

</body>
</html>
```